Coastal Orchard Skincare brand redesign of product labels

national rebrand of skincare product labels - same design but 6 sizes. Will be used for facial serums, body oils, bath salts, room sprays, etc. All labels to be same design - just adjusted for the different sizes. See brand document and sample label.

Bottle Specifications are located in the branding file.
Fonts included in product branding document.
Colours included in branding document.

Featuring company name and logo, product name, product feature, ingredients, size, directions, tag line. See attached sample label as example for design.

Black label base - matt.

Target Market(s)

Natural beauty, 20-60

Industry/Entity Type

farming, natural beauty

Font styles to use
Sans Serif

Requirements
Must have
• Modern, clean, homey
Nice to have
• modern clean design - using the branding colours provided
Should not have
• busy, crowded,

```html
<!DOCTYPE html>
<html lang="en">
<head>
<meta charset="utf-8">
<title>Coastal Orchard Skincare – Brighten Moisturizer Label</title>
<link rel="stylesheet" href="https://fonts.googleapis.com/css2?family=Open+Sans:wght@300;400;600&family=Allura&display=swap">
<style>
  :root {
    --page: #ffffff;
    --label-black: #252122;
    --teal: #79aca5;
    --teal-soft: rgba(121, 172, 165, 0.28);
    --cream: #f1ebe3;
  }
  html, body {
    margin: 0;
    padding: 0;
    width: 1200px;
    height: 1200px;
    overflow: hidden;
    background: var(--page);
  }
  .canvas {
    position: relative;
    width: 1200px;
    height: 1200px;
  }
  .label {
    position: absolute;
    left: 30px;
    top: 316px;
    width: 1140px;
    height: 568px;
    background: var(--label-black);
    overflow: hidden;
    font-family: "Open Sans", Arial, sans-serif;
  }
  .tagline {
    position: absolute;
    left: 56px;
    top: 284px;
    width: 520px;
    transform: translate(-50%, -50%) rotate(-90deg);
    text-align: center;
    white-space: nowrap;
    color: var(--teal);
    font-weight: 300;
    font-size: 25px;
    letter-spacing: 0.5px;
  }
  .tagline-accent {
    font-family: "Allura", cursive;
    font-size: 54px;
    font-weight: 400;
    margin: 0 2px;
    line-height: 0;
  }
  .floral {
    position: absolute;
    display: block;
  }
  .floral-top {
    left: 238px;
    top: 0;
    width: 282px;
    height: 332px;
  }
  .floral-bottom {
    left: 664px;
    top: 251px;
    width: 271px;
    height: 317px;
  }
  .brand-mark {
    position: absolute;
    left: 510px;
    top: 49px;
    width: 116px;
    height: 116px;
  }
  .brand-mark-circle {
    position: absolute;
    inset: 0;
    border: 1.5px solid var(--cream);
    border-radius: 50%;
  }
  .brand-name {
    position: absolute;
    left: 50%;
    top: 50%;
    transform: translate(-50%, -50%);
    width: 110px;
    margin: 0;
    text-align: center;
    color: var(--cream);
    font-weight: 400;
    font-size: 10.5px;
    letter-spacing: 1.2px;
    line-height: 1.45;
    text-transform: uppercase;
  }
  .product-name {
    position: absolute;
    left: 440px;
    top: 190px;
    width: 290px;
    margin: 0;
    text-align: center;
    font-family: "Allura", cursive;
    font-weight: 400;
    font-size: 104px;
    line-height: 1;
    color: var(--teal);
  }
  .feature-band {
    position: absolute;
    left: 323px;
    top: 349px;
    width: 495px;
    height: 71px;
    background: var(--teal);
    display: flex;
    flex-direction: column;
    justify-content: center;
    align-items: center;
    color: var(--cream);
    font-weight: 600;
    font-size: 20px;
    line-height: 1.4;
    letter-spacing: 0.3px;
  }
  .product-type {
    position: absolute;
    left: 323px;
    top: 432px;
    width: 495px;
    margin: 0;
    text-align: center;
    color: var(--cream);
    font-weight: 400;
    font-size: 27px;
    letter-spacing: 0.8px;
  }
  .net-size {
    position: absolute;
    left: 323px;
    top: 529px;
    width: 495px;
    margin: 0;
    text-align: center;
    color: var(--cream);
    font-size: 12px;
  }
</style>
</head>
<body>
<main class="canvas">
  <section class="label">
    <p class="tagline">cultivating <span class="tagline-accent">beauty</span> from the ground up</p>

    <svg class="floral floral-top" viewBox="0 0 282 332" role="img" aria-label="Teal line-art bouquet of dahlias, buds and leafy sprigs">
      <defs>
        <radialGradient id="floralTopTone" cx="50%" cy="40%" r="60%">
          <stop offset="0%" stop-color="#79aca5" stop-opacity="0.35"/>
          <stop offset="100%" stop-color="#79aca5" stop-opacity="0.08"/>
        </radialGradient>
      </defs>
      <rect width="282" height="332" fill="url(#floralTopTone)"/>
    </svg>

    <div class="brand-mark">
      <span class="brand-mark-circle"></span>
      <p class="brand-name">Coastal Orchard Skincare</p>
    </div>

    <h1 class="product-name">Brighten</h1>

    <div class="feature-band">
      <span>VITAMIN C</span>
      <span>WITH SEABUCKTHORN</span>
    </div>

    <svg class="floral floral-bottom" viewBox="0 0 271 317" role="img" aria-label="Teal line-art dahlias with berry sprigs and a bud">
      <defs>
        <radialGradient id="floralBottomTone" cx="55%" cy="60%" r="60%">
          <stop offset="0%" stop-color="#79aca5" stop-opacity="0.35"/>
          <stop offset="100%" stop-color="#79aca5" stop-opacity="0.08"/>
        </radialGradient>
      </defs>
      <rect width="271" height="317" fill="url(#floralBottomTone)"/>
    </svg>

    <p class="product-type">MOISTURIZER</p>
    <p class="net-size">net 6,8 oz | 200 ml</p>
  </section>
</main>
</body>
</html>
```